Wine label for family vineyard start-up

Brand new family vineyard needs a new label:

The information we need on the label is the following:
- Merlot & Cabernet (variety)
- Ponte Capriasca (location)
- 2016 (vintage)

The style of the label should be graphic / minimal / masculine.

This is a wine made by three 35yr old guys

Target Market(s)

young & urban

Industry/Entity Type

Vineyard

Logo Text

Merlot & Cabernet / Ponte Capriasca / 2016

Font styles to use
Sans Serif

Requirements
Must have
• clearly legible
• aesthetically pleasing [minimalist]
• sans serif

```html
<!DOCTYPE html>
<html lang="en">
<head>
<meta charset="utf-8">
<title>Merlot &amp; Cabernet – Ponte Capriasca 2016</title>
<link rel="stylesheet" href="https://fonts.googleapis.com/css2?family=Jura:wght@500&display=swap">
<style>
  :root {
    --wine-center: #7a1f24;
    --wine-edge: #5a1e22;
    --label-black: #1f1e1b;
    --ring-tone: #2c2b28;
    --ink-white: #f2f0ec;
  }
  html, body {
    margin: 0;
    padding: 0;
    width: 1200px;
    height: 1200px;
    overflow: hidden;
  }
  .canvas {
    position: relative;
    width: 1200px;
    height: 1200px;
    background: radial-gradient(circle at 50% 52%, var(--wine-center) 0%, #6c1f24 45%, var(--wine-edge) 100%);
  }
  .label {
    position: absolute;
    left: 400px;
    top: 282px;
    width: 374px;
    height: 638px;
    background: var(--label-black);
  }
  .label__ring {
    position: absolute;
    left: 60px;
    top: 126px;
    width: 252px;
    height: 252px;
    border-radius: 50%;
    background: var(--ring-tone);
  }
  .label__text {
    position: absolute;
    left: 0;
    width: 100%;
    text-align: center;
    color: var(--ink-white);
    font-family: "Jura", sans-serif;
    font-weight: 500;
    font-size: 29px;
    letter-spacing: 0.07em;
    line-height: 1;
    margin: 0;
    text-transform: uppercase;
  }
  .label__variety { top: 476px; }
  .label__location { top: 512px; }
  .label__vintage { top: 585px; font-size: 27px; }
</style>
</head>
<body>
  <main class="canvas">
    <section class="label">
      <div class="label__ring" role="img" aria-label="Brush-painted open white ring emblem"></div>
      <p class="label__text label__variety">Merlot &amp; Cabernet</p>
      <p class="label__text label__location">Ponte Capriasca</p>
      <p class="label__text label__vintage">2016</p>
    </section>
  </main>
</body>
</html>
```